Seed Oil Safety Card for Healthy Restaurant Dining

I am seeking a design for a physical card to communicate my wife's health-related dietary restriction regarding seed oils. This card will be given to restaurant waiters to ensure her meals are prepared without seed oils, as it is a health issue and not merely a preference.
My wife cannot eat any “seed oil” or “processed oil”, including:
- Vegetable oil
- Canola oil
- Soybean oil
- Sunflower oil
- Corn oil
- Cottonseed oil
- Safflower oil
- Peanut oil
- Sesame oil
Oils that are OK for her to consume:
- Butter (most preferable)
- Extra virgin olive oil
- Avocado oil
- Coconut oil
- Ghee
- Lard
- Any other animal-based fats
Key Design Requirements:
- Clarity and speed of communication: The card should be easily read and understood by waiters, even in low-light environments, emphasizing that it's a health concern.
- Avoid common misconceptions: Ensure the design doesn't imply common dietary preferences like "vegetarian" or "no butter." Animal fats and butter are actually preferable for her!
- Preferred term: Use "seed oils" as the term to describe what she cannot eat due to her health issue.
- Trace amounts are acceptable: Communicate that it's OK to use cookware that has previously been in contact with seed oils, but not to have seed oil as an ingredient. Please suggest a concise way to convey this.
- Card dimensions: Design should be 3.5” x 2.25” (standard credit-card size on printorvale.example). Horizontal or vertical layouts are both fine, whichever makes the message clearer.
Design Suggestions:
- Utilize bold and easy-to-read typography to communicate the main message.
- Consider incorporating relevant icons or graphics that help convey the message without adding confusion.
- Use contrasting colors to enhance readability, especially in low-light situations.
- To communicate the “trace amounts OK” part, consider phrases such as:
- "Cross-contamination acceptable"
- “Used cookware OK, no ingredient use”
- “Separate cookware not necessary”
Thank you for your assistance in creating this essential card for my wife's health and safety when dining out!

```html
<!DOCTYPE html>
<html lang="en">
<head>
<meta charset="utf-8">
<title>Seed Oil Allergy Card</title>
<link rel="stylesheet" href="https://fonts.googleapis.com/css2?family=Roboto+Condensed:ital,wght@0,500;0,700;1,500&display=swap">
<style>
  :root {
    --backdrop: #9a9a9a;
    --card: #ffffff;
    --ink: #111111;
    --no: #9b1c2a;
    --ok: #1a6b35;
  }
  html, body {
    margin: 0;
    width: 1200px;
    height: 1200px;
    overflow: hidden;
    background: var(--backdrop);
    font-family: "Roboto Condensed", "Arial Narrow", sans-serif;
  }
  .card {
    position: absolute;
    left: 138px;
    top: 302px;
    width: 923px;
    height: 595px;
    background: var(--card);
    border-radius: 38px;
  }
  .title {
    position: absolute;
    left: 0;
    right: 0;
    top: 24px;
    margin: 0;
    text-align: center;
    font-weight: 700;
    font-size: 60px;
    letter-spacing: 2px;
    line-height: 1;
    color: var(--ink);
  }
  .title-rule {
    position: absolute;
    left: 320px;
    top: 89px;
    width: 275px;
    height: 5px;
    background: var(--ink);
  }
  .verdict {
    position: absolute;
    top: 111px;
    width: 300px;
    text-align: center;
  }
  .verdict--no { left: 91px; }
  .verdict--ok { left: 525px; }
  .verdict svg { display: block; margin: 0 auto; }
  .verdict-label {
    margin: 10px 0 0;
    font-weight: 700;
    font-size: 35px;
    letter-spacing: 1.3px;
    line-height: 1.1;
    color: var(--ink);
  }
  .verdict .pointer { margin-top: 14px; }
  .oil-list {
    position: absolute;
    top: 274px;
    margin: 0;
    padding: 0;
    list-style: none;
    font-weight: 700;
    font-size: 27.5px;
    letter-spacing: 0.6px;
    line-height: 36.7px;
  }
  .oil-list li { position: relative; padding-left: 27px; white-space: nowrap; }
  .oil-list svg { position: absolute; left: 0; top: 11px; }
  .oil-list--no { color: var(--no); }
  .oil-list--ok { color: var(--ok); }
  .col-1 { left: 36px; }
  .col-2 { left: 241px; }
  .col-3 { left: 466px; }
  .col-4 { left: 702px; }
  .note {
    position: absolute;
    left: 0;
    right: 0;
    top: 508px;
    margin: 0;
    text-align: center;
    font-style: italic;
    font-weight: 500;
    font-size: 27px;
    letter-spacing: 0.9px;
    line-height: 30px;
    color: var(--ink);
  }
</style>
</head>
<body>
  <main class="card">
    <h1 class="title">SEED OIL ALLERGY!</h1>
    <div class="title-rule"></div>

    <section class="verdict verdict--no">
      <svg width="68" height="68" viewBox="0 0 68 68" aria-hidden="true">
        <rect x="2" y="2" width="64" height="64" rx="2" fill="none" stroke="var(--no)" stroke-width="4"/>
        <path d="M17 17 L51 51 M51 17 L17 51" stroke="var(--no)" stroke-width="9"/>
      </svg>
      <p class="verdict-label">Cannot Consume</p>
      <svg class="pointer" width="44" height="25" viewBox="0 0 44 25" aria-hidden="true"><path d="M0 0 H44 L22 25 Z" fill="var(--ink)"/></svg>
    </section>

    <section class="verdict verdict--ok">
      <svg width="68" height="68" viewBox="0 0 68 68" aria-hidden="true">
        <rect x="2" y="2" width="64" height="64" rx="2" fill="none" stroke="var(--ok)" stroke-width="4"/>
        <path d="M15 36 L28 49 L53 19" fill="none" stroke="var(--ok)" stroke-width="9"/>
      </svg>
      <p class="verdict-label">OK To Consume</p>
      <svg class="pointer" width="44" height="25" viewBox="0 0 44 25" aria-hidden="true"><path d="M0 0 H44 L22 25 Z" fill="var(--ink)"/></svg>
    </section>

    <svg width="0" height="0" style="position:absolute">
      <defs>
        <symbol id="mark-no" viewBox="0 0 16 16">
          <rect x="1" y="1" width="14" height="14" fill="none" stroke="currentColor" stroke-width="1.6"/>
          <path d="M5 5 L11 11 M11 5 L5 11" stroke="currentColor" stroke-width="2"/>
        </symbol>
        <symbol id="mark-ok" viewBox="0 0 16 16">
          <rect x="1" y="1" width="14" height="14" fill="none" stroke="currentColor" stroke-width="1.4"/>
          <path d="M4.5 8.5 L7 11 L11.5 5" fill="none" stroke="currentColor" stroke-width="1.6"/>
        </symbol>
      </defs>
    </svg>

    <ul class="oil-list oil-list--no col-1">
      <li><svg width="16" height="16"><use href="#mark-no"/></svg>Vegetable oil</li>
      <li><svg width="16" height="16"><use href="#mark-no"/></svg>Canola oil</li>
      <li><svg width="16" height="16"><use href="#mark-no"/></svg>Soybean oil</li>
      <li><svg width="16" height="16"><use href="#mark-no"/></svg>Sunflower oil</li>
      <li><svg width="16" height="16"><use href="#mark-no"/></svg>Corn oil</li>
    </ul>
    <ul class="oil-list oil-list--no col-2">
      <li><svg width="16" height="16"><use href="#mark-no"/></svg>Cottonseed oil</li>
      <li><svg width="16" height="16"><use href="#mark-no"/></svg>Safflower oil</li>
      <li><svg width="16" height="16"><use href="#mark-no"/></svg>Peanut oil</li>
      <li><svg width="16" height="16"><use href="#mark-no"/></svg>Sesame oil</li>
    </ul>
    <ul class="oil-list oil-list--ok col-3">
      <li><svg width="16" height="16"><use href="#mark-ok"/></svg>Butter<br>(most preferable)</li>
      <li><svg width="16" height="16"><use href="#mark-ok"/></svg>Extra virgin</li>
      <li><svg width="16" height="16"><use href="#mark-ok"/></svg>Olive oil</li>
      <li><svg width="16" height="16"><use href="#mark-ok"/></svg>Avocado oil</li>
    </ul>
    <ul class="oil-list oil-list--ok col-4">
      <li><svg width="16" height="16"><use href="#mark-ok"/></svg>Coconut oil</li>
      <li><svg width="16" height="16"><use href="#mark-ok"/></svg>Ghee</li>
      <li><svg width="16" height="16"><use href="#mark-ok"/></svg>Lard</li>
      <li><svg width="16" height="16"><use href="#mark-ok"/></svg>Any other<br>animal-based<br>fats</li>
    </ul>

    <p class="note">"Cross-contamination acceptable" “Used cookware OK, no ingredient use”<br>“Separate cookware not necessary"</p>
  </main>
</body>
</html>
```